Emerging automotive detailing business

I am starting a small automotive detailing business in hopes of becoming a well-known detailer to work on high end cars. I would like a card to reflect the high quality and time I put into my work. The name of the company is Bright Crest Detailing. I feel like it represents racecars getting off the line at the drag strip as well as an innuendo of "Up the Ladder". I do minor paint correction such as clay barring, multi-step buffing and polishing, waxing, hand washes, etc. I am always striving to learn more and improve my work. My goal is to have total customer satisfaction. This is a female run business but I do not want it to be very girly. Elegant is okay! I have pictures of my personal wrenfield attached, they do not need to be incorporated but if you can think of a cool way to use 1 or all of them, go for it!

Target Market(s)

Anyone that owns a vehicle. Preferably high end vehicles such as Valtori, Castellverde and Morvani but I will also happily work on any car, truck or suv no matter what brand.

Industry/Entity Type

Automotive

Contact Information for Business Card

Bright Crest Detailing
Mira Tolland
4175 Quenhollow Rd
Ashmere PA 17492
Cell phone- call/text- 717-555-0148
email- brightcrestdetails@maildrop-example.com
Instagram: @brightcrestdetailing
Facebook: facebook.com/brightcrestdetailing

Requirements
Must have
• Business name, my name, address, phone number. Listing that I do minor paint correction such as clay barring, multi-step buffing and polishing, waxing, hand washes, interior cleaning, and more. (This last part was in nice to haves but I have realized that I do really want it, so I moved it to must haves.) I want something that is different and eye-catching to my customers. Some people have done this very well with cards already submitted to me, but a lot have not. I didn't mess with the "look and feel bars" much because because I am pretty open to the overall design as long as it is not your basic run of the mill design.
Nice to have
• Something car related. Maybe an appointment time/date line. I do not have a logo, but if you would like to design one and incorporate it, that would be amazing!
Should not have
• Purple and Pink colors. Boring, basic, normal card.

```html
<!DOCTYPE html>
<html lang="en">
<head>
<meta charset="utf-8">
<title>Bright Crest Detailing – Business Card</title>
<link rel="stylesheet" href="https://fonts.googleapis.com/css2?family=Jost:wght@700&family=Lato:wght@300;400;700;900&display=swap">
<style>
  :root {
    --page-bg: #e6e3de;
    --card-front: #050505;
    --card-back: #f4f4f4;
    --ink: #ffffff;
    --ink-soft: #cfcfcf;
    --ink-dark: #111111;
    --rule: #a9a9a9;
    --photo-dark: #1d3a4a;
    --photo-deep: #0c1b24;
    --photo-green: #3f6b2a;
    --photo-green-deep: #1f3a14;
  }
  * { box-sizing: border-box; }
  html, body {
    margin: 0;
    width: 1200px;
    height: 1023px;
    overflow: hidden;
    background: var(--page-bg);
  }
  .card {
    position: absolute;
    left: 180px;
    width: 840px;
    height: 480px;
    overflow: hidden;
    box-shadow: 0 8px 24px rgba(0,0,0,.22);
  }

  /* ---------- Front ---------- */
  .card-front {
    top: 24px;
    background: var(--card-front);
    color: var(--ink);
  }
  .front-info {
    position: absolute;
    left: 56px;
    top: 48px;
    width: 600px;
  }
  .owner-name {
    margin: 0 0 14px;
    font-family: "Jost", sans-serif;
    font-weight: 700;
    font-size: 54px;
    line-height: 1.05;
  }
  .contact-group {
    font-family: "Lato", sans-serif;
    font-weight: 300;
    font-size: 21px;
    line-height: 1.4;
    color: var(--ink-soft);
    white-space: nowrap;
    text-align: center;
    padding: 0 0 14px;
    margin-bottom: 16px;
    border-bottom: 1.5px solid var(--rule);
  }
  .contact-group .label { font-weight: 400; color: var(--ink); }
  .group-phone   { width: 420px; margin-left: 60px; }
  .group-social  { width: 520px; margin-left: 40px; }
  .group-address { width: 420px; margin-left: 100px; border-bottom: none; }

  .company-banner {
    position: absolute;
    right: 40px;
    top: 30px;
    height: 420px;
    writing-mode: vertical-rl;
    border-left: 1.5px solid var(--rule);
    border-right: 1.5px solid var(--rule);
    padding: 0 10px;
    font-family: "Jost", sans-serif;
    font-weight: 700;
    font-size: 30px;
    letter-spacing: 1px;
    text-align: center;
  }

  /* ---------- Back ---------- */
  .card-back {
    top: 520px;
    background: var(--card-back);
    color: var(--ink-dark);
  }
  .photo-car {
    position: absolute;
    left: 0; top: 0;
    width: 300px; height: 100%;
    background: linear-gradient(160deg, #c9d3d8 0%, var(--photo-dark) 45%, var(--photo-deep) 100%);
  }
  .photo-foliage {
    position: absolute;
    right: 0; top: 0;
    width: 110px; height: 100%;
    background: linear-gradient(180deg, var(--photo-green) 0%, var(--photo-green-deep) 100%);
  }
  .back-panel {
    position: absolute;
    left: 340px;
    top: 44px;
    width: 350px;
    font-family: "Lato", sans-serif;
  }
  .appointment-title {
    margin: 0 0 18px;
    font-weight: 900;
    font-size: 30px;
  }
  .appointment-line {
    display: flex;
    align-items: flex-end;
    gap: 10px;
    margin-bottom: 20px;
    font-size: 18px;
    font-weight: 700;
  }
  .appointment-line span.fill {
    flex: 1;
    border-bottom: 1.5px solid var(--ink-dark);
    height: 20px;
  }
  .services {
    margin: 26px 0 0;
    padding-top: 16px;
    border-top: 1.5px solid var(--rule);
    font-size: 16px;
    font-weight: 400;
    line-height: 1.5;
    color: #333;
  }
</style>
</head>
<body>
  <section class="card card-front" aria-label="Business card front">
    <div class="front-info">
      <h1 class="owner-name">Mira Tolland</h1>
      <div class="contact-group group-phone">
        <div><span class="label">Cell/Text:</span> 717-555-0148</div>
        <div><span class="label">Instagram:</span> @brightcrestdetailing</div>
      </div>
      <div class="contact-group group-social">
        <div><span class="label">Facebook:</span> brightcrestdetailing</div>
        <div><span class="label">Email-</span> brightcrestdetails@maildrop-example.com</div>
      </div>
      <div class="contact-group group-address">
        <div>4175 Quenhollow Rd, Ashmere PA 17492</div>
      </div>
    </div>
    <div class="company-banner">Bright Crest Detailing</div>
  </section>

  <section class="card card-back" aria-label="Business card back">
    <div class="photo-car" role="img" aria-label="Photo of a detailed car"></div>
    <div class="back-panel">
      <h2 class="appointment-title">Next Appointment</h2>
      <div class="appointment-line">Date <span class="fill"></span></div>
      <div class="appointment-line">Time <span class="fill"></span></div>
      <p class="services">Clay barring · Multi-step buffing &amp; polishing · Waxing · Hand washes · Interior cleaning &amp; more</p>
    </div>
    <div class="photo-foliage" role="img" aria-label="Photo of greenery behind the car"></div>
  </section>
</body>
</html>
```